Volbrey Inc Business Card

Looking to get an updated business card for a Contract Machining company (www.volbreyinc.example) - looking for a clean design the portrays the technical nature of the business - colors can follow the website design and be in any combination that makes sense (red black, white, metallic or silver) - logos attached for use also. Would like space for: Name, title, business phone (555 214-3086), cell phone , website (www.volbreyinc.example) - possibly QR code could be integrated for website (designer choice), business address - 418 Harlow Bend, Alderbrook, ST 48199 (cards will be for 4 employees, I will either need to modify a template or I can provide individual information)
Target Market(s)
Aerospace, defense and medical device manufacturing companies that need machining
Industry/Entity Type
Machining for aerospace, defense, medical
Contact Information for Business Card
Name, Title, Business Phone, Cell Phone, email, business website and business address
Look and feel

```html
<!DOCTYPE html>
<html lang="en">
<head>
<meta charset="utf-8">
<title>Volbrey Inc Business Card</title>
<link rel="stylesheet" href="https://fonts.googleapis.com/css2?family=Montserrat:wght@400;500;800&display=swap">
<style>
  :root {
    --brand-red: #b31e25;
    --ink: #1c1c1c;
    --muted: #3a3a3a;
    --paper: #ffffff;
    --backdrop: #e9e6e1;
  }
  * { box-sizing: border-box; margin: 0; padding: 0; }
  html, body { width: 1200px; height: 931px; overflow: hidden; }
  body {
    background: var(--backdrop);
    font-family: "Montserrat", Arial, sans-serif;
    position: relative;
  }
  .card {
    position: absolute;
    width: 600px;
    height: 343px;
    border-radius: 18px;
    overflow: hidden;
    box-shadow: 0 10px 24px rgba(0,0,0,0.25);
  }
  .card-back {
    left: 70px; top: 90px;
    background: var(--brand-red);
    display: flex; align-items: center; justify-content: center;
  }
  .back-mark {
    width: 200px; height: 200px;
    border-radius: 50%;
    background: var(--paper);
    display: flex; align-items: center; justify-content: center;
  }
  .back-mark .wordmark {
    color: var(--brand-red);
    font-weight: 800;
    font-size: 30px;
    letter-spacing: 1px;
  }
  .card-front {
    left: 530px; top: 480px;
    background: var(--paper);
  }
  .front-brand {
    position: absolute;
    right: 42px; top: 24px;
    display: flex; flex-direction: column; align-items: center;
  }
  .brand-circle {
    width: 108px; height: 108px;
    border-radius: 50%;
    background: var(--brand-red);
  }
  .front-brand .wordmark {
    margin-top: 10px;
    color: var(--brand-red);
    font-weight: 800;
    font-size: 30px;
    letter-spacing: 1px;
  }
  .divider {
    position: absolute;
    left: 40px; right: 30px; top: 200px;
    height: 1.5px;
    background: var(--brand-red);
  }
  .person {
    position: absolute;
    left: 40px; top: 142px;
  }
  .person-name {
    color: var(--brand-red);
    font-weight: 800;
    font-size: 28px;
    line-height: 1.1;
  }
  .person-title {
    color: var(--muted);
    font-weight: 400;
    font-size: 15px;
    margin-top: 2px;
  }
  .contacts {
    position: absolute;
    left: 40px; top: 212px;
    list-style: none;
  }
  .contacts li {
    display: flex; align-items: center; gap: 10px;
    color: var(--ink);
    font-size: 15px;
    line-height: 24px;
  }
  .contacts svg { width: 15px; height: 15px; fill: var(--brand-red); flex: none; }
  .address {
    position: absolute;
    right: 40px; top: 236px;
    text-align: right;
    font-size: 14px;
    line-height: 19px;
    font-style: normal;
    color: var(--ink);
  }
  .base-band {
    position: absolute;
    left: 0; right: 0; bottom: 0;
    height: 20px;
    background: var(--brand-red);
  }
</style>
</head>
<body>

<section class="card card-back" aria-label="Card back">
  <div class="back-mark"><span class="wordmark">VOLBREY</span></div>
</section>

<section class="card card-front" aria-label="Card front">
  <div class="front-brand">
    <div class="brand-circle"></div>
    <span class="wordmark">VOLBREY</span>
  </div>

  <div class="person">
    <h1 class="person-name">Dana Whitlock</h1>
    <p class="person-title">Owner</p>
  </div>
  <div class="divider"></div>

  <ul class="contacts">
    <li>
      <svg viewBox="0 0 24 24" aria-hidden="true"><path d="M6.6 10.8a15.1 15.1 0 0 0 6.6 6.6l2.2-2.2a1 1 0 0 1 1-.25 11.4 11.4 0 0 0 3.6.57 1 1 0 0 1 1 1V20a1 1 0 0 1-1 1A17 17 0 0 1 3 4a1 1 0 0 1 1-1h3.5a1 1 0 0 1 1 1c0 1.250.2 2.45.57 3.57a1 1 0 0 1-.25 1z"/></svg>
      555 214-3086
    </li>
    <li>
      <svg viewBox="0 0 24 24" aria-hidden="true"><path d="M7 2h10a2 2 0 0 1 2 2v16a2 2 0 0 1-2 2H7a2 2 0 0 1-2-2V4a2 2 0 0 1 2-2zm0 3v13h10V5zm5 14.2a1 1 0 1 0 0 .01z"/></svg>
      555 214-3086
    </li>
    <li>
      <svg viewBox="0 0 24 24" aria-hidden="true"><path d="M3 5h18a1 1 0 0 1 1 1v12a1 1 0 0 1-1 1H3a1 1 0 0 1-1-1V6a1 1 0 0 1 1-1zm1 2.2V17h16V7.2l-8 5.3z M4.5 7h15L12 11.9z"/></svg>
      info@volbreyinc.example
    </li>
    <li>
      <svg viewBox="0 0 24 24" aria-hidden="true"><path d="M12 2a10 10 0 1 0 0 20 10 10 0 0 0 0-20zm6.9 9h-3a15 15 0 0 0-1.3-5.6A8 8 0 0 1 18.9 11zM12 4.1c.9 1.2 1.8 3.6 1.9 6.9h-3.8c.1-3.3 1-5.7 1.9-6.9zM9.4 5.4A15 15 0 0 0 8.1 11h-3a8 8 0 0 1 4.3-5.6zM5.1 13h3a15 15 0 0 0 1.3 5.6A8 8 0 0 1 5.1 13zm6.9 6.9c-.9-1.2-1.8-3.6-1.9-6.9h3.8c-.1 3.3-1 5.7-1.9 6.9zm2.6-1.3a15 15 0 0 0 1.3-5.6h3a8 8 0 0 1-4.3 5.6z"/></svg>
      www.volbreyinc.example
    </li>
  </ul>

  <address class="address">
    418 Harlow Bend,<br>
    Alderbrook, ST 48199
  </address>

  <div class="base-band"></div>
</section>

</body>
</html>
```